Games for Pupils Website Redesign

The purpose of the website redesign is to freshen up the content and update it to give a more modern look and feel. It will show what we do concisely and satisfy all potential visitors. We work with primary schools and the brand is fun.About: Games for Pupils is a scheme that brings top Olympic athletes into primary schools to inspire children to do more physical activity. We typically run a half day event at the school where the athlete does a fun fitness circuit with the children and then an inspirational assembly with a demonstration and Q&A. The children are asked to collect sponsorship money to take part in the event and a large proportion of the money raised goes back to the school in the form of a voucher for them to spend on new sports equipment. 1. To generate more leads from potential customers/schools2. To engage the children and parents more in the event and get them excited for their upcoming visit whilst setting up a fundraiser page.3. To simplify and modernise what is already there.

I have attached some ideas for each of the pages (uploaded in brief)

Here is a link to our current website: www.gamesforpupils.example

I have also attached a link to the sponsorship form which shows the kind of look and feel we're after.

Target Market(s)

Primary school teachers
Primary school parents

Number of Pages Required

5+ page

Requirements
Must have
• Fun, modern.
• Be built on kestrel framekit

```html
<!DOCTYPE html>
<html lang="en">
<head>
<meta charset="utf-8">
<title>Games for Pupils – I'm a School</title>
<link href="https://fonts.googleapis.com/css2?family=Montserrat:wght@400;500;600;700;800&display=swap" rel="stylesheet">
<style>
:root{
  --ink:#111111;
  --text:#333333;
  --white:#ffffff;
  --mint-soft:#dff6da;
  --green:#3dcd1f;
  --red:#e81b31;
  --blue:#17a1fa;
  --orange:#ff6f2b;
  --footer:#1e1e1e;
  --footer-text:#e8e8e8;
}
*{margin:0;padding:0;box-sizing:border-box}
html,body{width:720px;height:1200px;overflow:hidden;background:var(--white)}
body{font-family:'Montserrat',sans-serif;color:var(--text);position:relative}
.page{position:relative;width:720px;height:1200px}

.decor-area{position:absolute;z-index:1;border-radius:18px;background:linear-gradient(135deg,var(--mint-soft),#eafaE6)}

.site-header{position:absolute;left:0;top:0;width:720px;height:56px;background:var(--white);border-bottom:1px solid #f1f1f1;z-index:3}
.brand{position:absolute;left:40px;top:22px;display:flex;align-items:center;gap:5px;font-weight:700;font-size:10px;color:var(--ink)}
.brand-dot{width:11px;height:11px;border-radius:50%;background:var(--red)}
.menu-toggle{position:absolute;left:632px;top:25px;display:flex;align-items:center;gap:8px;font-weight:700;font-size:7.5px;letter-spacing:.8px;color:var(--ink)}
.menu-lines{display:flex;flex-direction:column;gap:3px}
.menu-lines span{display:block;width:22px;height:2px}
.menu-lines span:nth-child(1){background:var(--green)}
.menu-lines span:nth-child(2){background:var(--red)}
.menu-lines span:nth-child(3){background:var(--blue)}

.page-title{position:absolute;left:0;top:103px;width:720px;text-align:center;font-weight:700;font-size:18px;color:var(--ink);z-index:2}
.intro{position:absolute;left:190px;top:189px;width:340px;text-align:center;font-weight:700;font-size:10.4px;line-height:13.3px;color:var(--ink);text-transform:uppercase;z-index:2}

.feature-badge{position:absolute;width:190px;height:190px;z-index:2}
.feature-badge text{font-family:'Montserrat',sans-serif;font-weight:700;font-size:17px;fill:var(--white)}
.feature-copy{position:absolute;width:208px;font-size:6.6px;line-height:9.4px;color:var(--text);z-index:2}
.feature-copy.right{text-align:right}

.site-footer{position:absolute;left:0;top:980px;width:720px;height:220px;background:var(--footer);color:var(--footer-text);text-align:center;font-size:5.6px;letter-spacing:.4px;z-index:3}
.footer-nav{position:absolute;top:23px;width:100%;font-weight:500}
.footer-brand{position:absolute;top:60px;width:100%;display:flex;justify-content:center;align-items:center;gap:5px;font-weight:700;font-size:9px;color:var(--white)}
.footer-brand .brand-dot{width:9px;height:9px}
.footer-legal{position:absolute;top:86px;width:100%;line-height:8px}
.footer-contact{position:absolute;top:115px;width:100%;line-height:8.6px}
.footer-contact .label{color:var(--green)}
.footer-social{position:absolute;top:165px;width:100%;display:flex;justify-content:center;gap:7px}
.social-link{display:block;width:11px;height:11px;background:var(--green);border-radius:1px}
.copyright{position:absolute;top:194px;width:100%}
</style>
</head>
<body>
<div class="page">

  <div class="decor-area" style="left:332px;top:56px;width:104px;height:36px;border-radius:0 0 52px 52px" role="img" aria-label="Decorative ring shape"></div>
  <div class="decor-area" style="left:640px;top:86px;width:80px;height:112px;border-radius:56px 0 0 56px" role="img" aria-label="Decorative ring shape"></div>
  <div class="decor-area" style="left:0;top:170px;width:138px;height:84px" role="img" aria-label="Decorative wavy lines"></div>
  <div class="decor-area" style="left:548px;top:322px;width:72px;height:128px" role="img" aria-label="Decorative triangle shape"></div>
  <div class="decor-area" style="left:22px;top:467px;width:125px;height:121px" role="img" aria-label="Decorative triangle shape"></div>
  <div class="decor-area" style="left:98px;top:794px;width:56px;height:56px;border-radius:50%" role="img" aria-label="Decorative ring shape"></div>
  <div class="decor-area" style="left:578px;top:818px;width:142px;height:76px" role="img" aria-label="Decorative wavy lines"></div>

  <header class="site-header">
    <div class="brand"><span class="brand-dot"></span>Games for Pupils</div>
    <div class="menu-toggle"><div class="menu-lines"><span></span><span></span><span></span></div>MENU</div>
  </header>

  <h1 class="page-title">I’M A SCHOOL</h1>
  <p class="intro">Lorem ipsum dolor sit amet, consectetur adipiscing elit, sed do eiusmod tempor incididunt ut labore et dolore magna aliqua. Quis ipsum suspendisse</p>

  <svg class="feature-badge" style="left:137px;top:275px" viewBox="-95 -95 190 190" role="img" aria-label="Activate">
    <circle cx="0" cy="0" r="64" fill="var(--red)"/>
    <circle cx="-7" cy="3" r="67" fill="none" stroke="var(--ink)" stroke-width="1.6"/>
    <text x="0" y="6" text-anchor="middle">ACTIVATE</text>
  </svg>
  <p class="feature-copy" style="left:334px;top:332px">Lorem ipsum dolor sit amet, consectetur adipiscing elit, sed do eiusmod tempor incididunt ut labore et dolore magna aliqua. Quis ipsum suspendisse ultrices gravida. Risus commodo viverra maecenas accumsan lacus vel facilisis. Lorem ipsum dolor sit amet, consectetur adipiscing elit, sed do eiusmod tempor incididunt ut labore et dolore magna aliqua. Quis ipsum suspendisse ultrices gravida. Risus commodo viverra maecenas accumsan lacus vel facilisis.</p>

  <svg class="feature-badge" style="left:405px;top:423px" viewBox="-95 -95 190 190" role="img" aria-label="Educate">
    <circle cx="0" cy="0" r="64" fill="var(--green)"/>
    <circle cx="-7" cy="3" r="67" fill="none" stroke="var(--ink)" stroke-width="1.6"/>
    <text x="0" y="6" text-anchor="middle">EDUCATE</text>
  </svg>
  <p class="feature-copy right" style="left:187px;top:482px">Lorem ipsum dolor sit amet, consectetur adipiscing elit, sed do eiusmod tempor incididunt ut labore et dolore magna aliqua. Quis ipsum suspendisse ultrices gravida. Risus commodo viverra maecenas accumsan lacus vel facilisis. Lorem ipsum dolor sit amet, consectetur adipiscing elit, sed do eiusmod tempor incididunt ut labore et dolore magna aliqua. Quis ipsum suspendisse ultrices gravida. Risus commodo viverra maecenas accumsan lacus vel facilisis.</p>

  <svg class="feature-badge" style="left:135px;top:571px" viewBox="-95 -95 190 190" role="img" aria-label="Motivate">
    <circle cx="0" cy="0" r="64" fill="var(--blue)"/>
    <circle cx="-7" cy="3" r="67" fill="none" stroke="var(--ink)" stroke-width="1.6"/>
    <text x="0" y="6" text-anchor="middle">MOTIVATE</text>
  </svg>
  <p class="feature-copy" style="left:334px;top:632px">Lorem ipsum dolor sit amet, consectetur adipiscing elit, sed do eiusmod tempor incididunt ut labore et dolore magna aliqua. Quis ipsum suspendisse ultrices gravida. Risus commodo viverra maecenas accumsan lacus vel facilisis. Lorem ipsum dolor sit amet, consectetur adipiscing elit, sed do eiusmod tempor incididunt ut labore et dolore magna aliqua. Quis ipsum suspendisse ultrices gravida. Risus commodo viverra maecenas accumsan lacus vel facilisis.</p>

  <svg class="feature-badge" style="left:405px;top:719px" viewBox="-95 -95 190 190" role="img" aria-label="Innovate">
    <circle cx="0" cy="0" r="64" fill="var(--orange)"/>
    <circle cx="-7" cy="3" r="67" fill="none" stroke="var(--ink)" stroke-width="1.6"/>
    <text x="0" y="6" text-anchor="middle">INNOVATE</text>
  </svg>
  <p class="feature-copy right" style="left:187px;top:774px">Lorem ipsum dolor sit amet, consectetur adipiscing elit, sed do eiusmod tempor incididunt ut labore et dolore magna aliqua. Quis ipsum suspendisse ultrices gravida. Risus commodo viverra maecenas accumsan lacus vel facilisis. Lorem ipsum dolor sit amet, consectetur adipiscing elit, sed do eiusmod tempor incididunt ut labore et dolore magna aliqua. Quis ipsum suspendisse ultrices gravida. Risus commodo viverra maecenas accumsan lacus vel facilisis.</p>

  <footer class="site-footer">
    <nav class="footer-nav">SITEMAP I COOKIES I PRIVACY POLICY I ONLINE FUNDRAISING</nav>
    <div class="footer-brand"><span class="brand-dot"></span>Games for Pupils</div>
    <p class="footer-legal">Games for Pupils and GFP Coaching are trading names of the Social Enterprise<br>called Playwell Ventures Limited, a company registered in England no. 09123456.</p>
    <p class="footer-contact">
      <span class="label">Telephone:</span> 01632 960 418 (GB) or 01 555 0192 (Ireland)<br>
      <span class="label">Email:</span> hello@gamesforpupils.example<br>
      <span class="label">Snailmail (we love a letter!):</span><br>
      GAMES for PUPILS 7 The Granary, Elmfield Park, Northbrook NB4 2QT<br>
      GAMES for PUPILS Harbour House, Quay Street, Westport 5 Ireland
    </p>
    <div class="footer-social">
      <svg class="social-link" viewBox="0 0 11 11" role="img" aria-label="Share">
        <rect width="11" height="11" rx="1" fill="var(--green)"/>
        <g fill="var(--white)" stroke="var(--white)" stroke-width=".8">
          <circle cx="3" cy="5.5" r="1.1"/><circle cx="8" cy="3" r="1.1"/><circle cx="8" cy="8" r="1.1"/>
          <path d="M3 5.5 L8 3 M3 5.5 L8 8" fill="none"/>
        </g>
      </svg>
      <svg class="social-link" viewBox="0 0 11 11" role="img" aria-label="Email">
        <rect width="11" height="11" rx="1" fill="var(--green)"/>
        <rect x="2" y="3" width="7" height="5" fill="none" stroke="var(--white)" stroke-width=".8"/>
        <path d="M2 3 L5.5 5.8 L9 3" fill="none" stroke="var(--white)" stroke-width=".8"/>
      </svg>
      <svg class="social-link" viewBox="0 0 11 11" role="img" aria-label="Website">
        <rect width="11" height="11" rx="1" fill="var(--green)"/>
        <g fill="none" stroke="var(--white)" stroke-width=".8">
          <circle cx="5.5" cy="5.5" r="3.3"/><ellipse cx="5.5" cy="5.5" rx="1.4" ry="3.3"/><path d="M2.2 5.5 H8.8"/>
        </g>
      </svg>
    </div>
    <p class="copyright">© 2019 GAMES FOR PUPILS</p>
  </footer>
</div>
</body>
</html>
```